Specialised investor in e-mobility and energy wants business card design

We need a business card design that fits our existing corporate design. <The look and feel must be 'sharp'/'clean', dynamic, communicate momentum, professionalism etc (as one would imagine from a firm in the financial sector). We like the idea of a reverse-side of the card that includes the logo, and the name and contact details on the other. We expect the deliverable to be whatever format might be required to be able to get cards printed directly by a service such as kelmo press. Our website is www.zub.capital

```html
<!DOCTYPE html>
<html lang="en">
<head>
<meta charset="utf-8">
<title>ZUB Capital – Business Card</title>
<link href="https://fonts.googleapis.com/css2?family=Roboto:wght@300;400;700&display=swap" rel="stylesheet">
<style>
  :root {
    --stage: #979797;
    --forest: #2d5020;
    --forest-deep: #264a1a;
    --leaf: #7cb342;
    --gold: #dcb892;
    --ink: #2e4a1e;
    --grey-text: #7a7a7a;
    --rule: #cfcfcf;
    --paper: #ffffff;
  }
  * { margin: 0; padding: 0; box-sizing: border-box; }
  html, body {
    width: 1200px; height: 1000px; overflow: hidden;
    background: var(--stage);
    font-family: "Roboto", Arial, sans-serif;
  }
  .card {
    position: absolute;
    left: 293px;
    width: 615px;
    height: 351px;
  }
  .card-front {
    top: 100px;
    background: var(--forest);
    display: flex; align-items: center; justify-content: center;
  }
  .front-wordmark {
    color: var(--gold);
    font-weight: 300;
    font-size: 58px;
    letter-spacing: 1px;
    margin-top: -22px;
  }
  .card-back {
    top: 511px;
    background: var(--paper);
    border-bottom: 10px solid var(--forest-deep);
    height: 351px;
  }
  .back-wordmark {
    position: absolute; left: 20px; top: 52px;
    color: var(--forest-deep);
    font-weight: 300;
    font-size: 28px;
  }
  .holder { position: absolute; left: 30px; top: 168px; }
  .holder-name { color: var(--ink); font-weight: 700; font-size: 22px; line-height: 28px; }
  .holder-role { color: var(--leaf); font-weight: 300; font-size: 22px; line-height: 28px; }
  .divider {
    position: absolute; left: 30px; right: 28px; top: 243px;
    border-top: 1px solid var(--rule);
  }
  .contacts {
    position: absolute; top: 268px;
    list-style: none;
    color: var(--grey-text);
    font-size: 18px;
  }
  .contacts li { display: flex; align-items: center; gap: 8px; height: 28px; }
  .contacts svg { width: 16px; height: 16px; fill: var(--leaf); flex: none; }
  .contacts-left { left: 30px; }
  .contacts-right { right: 28px; top: 271px; }
</style>
</head>
<body>
  <section class="card card-front">
    <div class="front-wordmark">ZUB Capital</div>
  </section>

  <section class="card card-back">
    <div class="back-wordmark">ZUB Capital</div>

    <div class="holder">
      <div class="holder-name">Martin Elsberg</div>
      <div class="holder-role">Partner</div>
    </div>

    <div class="divider"></div>

    <ul class="contacts contacts-left">
      <li>
        <svg viewBox="0 0 16 16" aria-hidden="true"><path d="M4 0h8a1 1 0 0 1 1 1v14a1 1 0 0 1-1 1H4a1 1 0 0 1-1-1V1a1 1 0 0 1 1-1zm1 2v10h6V2zm3 11a1 1 0 1 0 0 2 1 1 0 0 0 0-2z"/></svg>
        +41 79555 0148
      </li>
      <li>
        <svg viewBox="0 0 16 16" aria-hidden="true"><path d="M0 3h16v1L8 9 0 4zm0 2.5 8 5 8-5V13H0z"/></svg>
        martin@zub.capital
      </li>
    </ul>

    <ul class="contacts contacts-right">
      <li>
        <svg viewBox="0 0 16 16" aria-hidden="true"><path d="M8 0a8 8 0 1 0 0 16A8 8 0 0 0 8 0zm5.9 7h-2.4a12 12 0 0 0-.9-4.6A6 6 0 0 1 13.9 7zM8 2c.7.8 1.4 2.6 1.5 5h-3C6.6 4.6 7.3 2.8 8 2zM5.4 2.4A12 12 0 0 0 4.5 7H2.1a6 6 0 0 1 3.3-4.6zM2.1 9h2.4a12 12 0 0 0 .9 4.6A6 6 0 0 1 2.1 9zM8 14c-.7-.8-1.4-2.6-1.5-5h3c-.1 2.4-.8 4.2-1.5 5zm2.6-.4a12 12 0 0 0 .9-4.6h2.4a6 6 0 0 1-3.3 4.6z"/></svg>
        www.zub.capital
      </li>
      <li>
        <svg viewBox="0 0 16 16" aria-hidden="true"><path d="M8 0a5.5 5.5 0 0 0-5.5 5.5C2.5 10 8 16 8 16s5.5-6 5.5-10.5A5.5 5.5 0 0 0 8 0zm0 7.7a2.2 2.2 0 1 1 0-4.4 2.2 2.2 0 0 1 0 4.4z"/></svg>
        Lausanne, Switzerland
      </li>
    </ul>
  </section>
</body>
</html>
```